New Business Card Design Project

Use the flyer uploaded and website www.brightoakbuilders.com for inspiration.
List Our Services on Backside of business cards
Marcus Delling
Harborline Builders Inc.
Licensed General Contractors
858-471-6093

Contact Information for Business Card

Use the flyer uploaded and website www.brightoakbuilders.com for inspiration. List Our Services on Backside of business cards Marcus Delling Harborline Builders Inc. Licensed General Contractors 858-471-6093

```html
<!DOCTYPE html>
<html lang="en">
<head>
<meta charset="utf-8">
<title>Harborline Builders – Business Card</title>
<link rel="stylesheet" href="https://fonts.googleapis.com/css2?family=Roboto:wght@400;500;700&family=Roboto+Condensed:wght@700&display=swap">
<style>
  :root {
    --page-bg: #e9e9e9;
    --card-bg: #ffffff;
    --brand-red: #ed1c24;
    --brand-blue: #5583c6;
    --ink: #1a1a1a;
  }
  * { box-sizing: border-box; margin: 0; padding: 0; }
  html, body { width: 1200px; height: 780px; overflow: hidden; }
  body {
    background: var(--page-bg);
    font-family: "Roboto", sans-serif;
    color: var(--ink);
    position: relative;
  }
  .card {
    position: absolute;
    left: 328px;
    width: 545px;
    height: 312px;
    background: var(--card-bg);
    border-radius: 20px;
    border-left: 2px solid var(--brand-red);
    border-bottom: 2px solid var(--brand-red);
    box-shadow: 0 6px 16px rgba(0,0,0,.25);
    overflow: hidden;
  }
  .card--services { top: 62px; }
  .card--contact { top: 405px; }

  .wordmark {
    position: absolute;
    display: flex;
    align-items: center;
    gap: 8px;
    font-weight: 400;
    color: var(--ink);
    letter-spacing: 1.5px;
    white-space: nowrap;
  }
  .wordmark__square { width: 12px; height: 12px; background: var(--ink); }
  .card--services .wordmark { top: 128px; left: 0; right: 0; justify-content: center; font-size: 24px; }
  .card--contact .wordmark { top: 180px; left: 20px; width: 232px; justify-content: center; font-size: 18px; }

  .guarantee {
    position: absolute; top: 200px; left: 0; right: 0; text-align: center;
    font-family: "Roboto Condensed", sans-serif; font-weight: 700;
    font-size: 15px; color: var(--brand-red); letter-spacing: .2px;
  }
  .specialty {
    position: absolute; top: 218px; left: 18px; right: 18px;
    display: flex; align-items: center; gap: 6px;
  }
  .specialty__rule { flex: 1; height: 2px; background: linear-gradient(90deg, transparent, var(--brand-blue)); }
  .specialty__rule--right { background: linear-gradient(90deg, var(--brand-blue), transparent); }
  .specialty__title {
    font-family: "Roboto Condensed", sans-serif; font-weight: 700;
    font-size: 15px; color: var(--brand-blue);
  }
  .service-list {
    position: absolute; top: 238px; left: 0; right: 0;
    text-align: center; font-size: 11.6px; line-height: 17.3px;
  }
  .service-list__row { white-space: nowrap; }
  .service { display: inline-flex; align-items: center; gap: 3px; margin: 0 2px; }
  .service svg { width: 9px; height: 9px; }

  .divider {
    position: absolute; left: 270px; top: 56px; width: 2px; height: 200px;
    background: var(--brand-red);
  }
  .person { position: absolute; left: 321px; top: 70px; }
  .person__name { font-size: 31px; font-weight: 700; color: var(--brand-red); line-height: 1; }
  .person__role { font-size: 12px; margin-top: 3px; }
  .person__company { font-size: 12.4px; margin-top: 28px; }
  .contact-list { list-style: none; margin-top: 14px; font-size: 12.4px; }
  .contact-list li { display: flex; align-items: center; gap: 8px; height: 18.5px; }
  .contact-list svg { width: 13px; height: 13px; }

  .footer-bands { position: absolute; left: 0; top: 271px; width: 545px; height: 20px; }
</style>
</head>
<body>

<section class="card card--services">
  <div class="wordmark"><span class="wordmark__square"></span>HARBORLINE BUILDERS</div>
  <p class="guarantee">OUR SERVICES ARE 100% GUARANTEED</p>
  <div class="specialty">
    <span class="specialty__rule"></span>
    <span class="specialty__title">SPECIALIZING IN:</span>
    <span class="specialty__rule specialty__rule--right"></span>
  </div>
  <div class="service-list">
    <div class="service-list__row">
      <span class="service"><svg viewBox="0 0 10 10"><circle cx="5" cy="5" r="4" fill="none" stroke="#ed1c24"/><path d="M3 5l1.6 1.6L8 2.5" fill="none" stroke="#ed1c24" stroke-width="1.2"/></svg>Remodel: Kitchen &amp; Bath</span>
      <span class="service"><svg viewBox="0 0 10 10"><circle cx="5" cy="5" r="4" fill="none" stroke="#ed1c24"/><path d="M3 5l1.6 1.6L8 2.5" fill="none" stroke="#ed1c24" stroke-width="1.2"/></svg>Painting: Interior &amp; Exterior</span>
      <span class="service"><svg viewBox="0 0 10 10"><circle cx="5" cy="5" r="4" fill="none" stroke="#ed1c24"/><path d="M3 5l1.6 1.6L8 2.5" fill="none" stroke="#ed1c24" stroke-width="1.2"/></svg>Flooring: Carpet, Vinyl, Wood</span>
    </div>
    <div class="service-list__row">
      <span class="service"><svg viewBox="0 0 10 10"><circle cx="5" cy="5" r="4" fill="none" stroke="#ed1c24"/><path d="M3 5l1.6 1.6L8 2.5" fill="none" stroke="#ed1c24" stroke-width="1.2"/></svg>Window &amp; Door Replacement</span>
      <span class="service"><svg viewBox="0 0 10 10"><circle cx="5" cy="5" r="4" fill="none" stroke="#ed1c24"/><path d="M3 5l1.6 1.6L8 2.5" fill="none" stroke="#ed1c24" stroke-width="1.2"/></svg>Plumbing: Repairs &amp; Upgrades</span>
      <span class="service"><svg viewBox="0 0 10 10"><circle cx="5" cy="5" r="4" fill="none" stroke="#ed1c24"/><path d="M3 5l1.6 1.6L8 2.5" fill="none" stroke="#ed1c24" stroke-width="1.2"/></svg>Energy-Efficient Upgrades</span>
    </div>
    <div class="service-list__row">
      <span class="service"><svg viewBox="0 0 10 10"><circle cx="5" cy="5" r="4" fill="none" stroke="#ed1c24"/><path d="M3 5l1.6 1.6L8 2.5" fill="none" stroke="#ed1c24" stroke-width="1.2"/></svg>Deck &amp; Patio Construction</span>
      <span class="service"><svg viewBox="0 0 10 10"><circle cx="5" cy="5" r="4" fill="none" stroke="#ed1c24"/><path d="M3 5l1.6 1.6L8 2.5" fill="none" stroke="#ed1c24" stroke-width="1.2"/></svg>Water &amp; Mold Damage</span>
      <span class="service"><svg viewBox="0 0 10 10"><circle cx="5" cy="5" r="4" fill="none" stroke="#ed1c24"/><path d="M3 5l1.6 1.6L8 2.5" fill="none" stroke="#ed1c24" stroke-width="1.2"/></svg>Garage Renovation</span>
    </div>
  </div>
</section>

<section class="card card--contact">
  <div class="wordmark"><span class="wordmark__square"></span>HARBORLINE BUILDERS</div>
  <span class="divider"></span>
  <div class="person">
    <h1 class="person__name">Marcus Delling</h1>
    <p class="person__role">Licensed General Contractors</p>
    <p class="person__company">Harborline Builders Inc.</p>
    <ul class="contact-list">
      <li><svg viewBox="0 0 24 24"><path fill="#ed1c24" d="M6.6 10.8a15 15 0 006.6 6.6l2.2-2.2a1 1 0 011-.25 11.4 11.4 0 003.6.57 1 1 0 011 1V20a1 1 0 01-1 1A17 17 0 013 4a1 1 0 011-1h3.5a1 1 0 011 1c0 1.25.2 2.45.57 3.57a1 1 0 01-.25 1z"/></svg>858-471-6093</li>
      <li><svg viewBox="0 0 24 24"><path fill="#ed1c24" d="M2 5h20v14H2z"/><path d="M2 5l10 8 10-8" fill="none" stroke="#fff" stroke-width="2"/></svg>info@brightoakbuilders.com</li>
      <li><svg viewBox="0 0 24 24"><circle cx="12" cy="12" r="10" fill="#ed1c24"/><path d="M2 12h20M12 2c3 3 3 17 0 20M12 2c-3 3-3 17 0 20" fill="none" stroke="#fff" stroke-width="1.3"/></svg>www.brightoakbuilders.com</li>
    </ul>
  </div>
  <svg class="footer-bands" viewBox="0 0 545 20" aria-hidden="true">
    <path d="M0 0H240Q248 0 255 4L277 20H0Z" fill="var(--brand-red)"/>
    <path d="M264 0H545V20H298Q290 20 283 15Z" fill="var(--brand-blue)"/>
  </svg>
</section>

</body>
</html>
```